Tech business card design

We need an amazing business card design for our new business 'Pexla' a marketing tech startup based in Sydney, Australia. We provide an online marketplace for businesses to search and buy advertising media, connect with service providers and learn more about marketing. We wish to communicate 'cool tech', reliability and professionalism and design based around our logo.

Target Market(s)

Business Owners

Contact Information for Business Card

Name
Position
Email Address
Website
Phone Number

Font styles to use
Other font styles liked:
• Avenir & Avenir Next

Colors

Designer to choose colors to be used in the design.

```html
<!DOCTYPE html>
<html lang="en">
<head>
<meta charset="utf-8">
<title>Pexla Business Card</title>
<link rel="stylesheet" href="https://fonts.googleapis.com/css2?family=Open+Sans:wght@400;700;800&display=swap">
<style>
  :root {
    --backdrop: #a0cee2;
    --card-light: #ffffff;
    --card-dark: #111338;
    --card-dark-edge: #3c4148;
    --ink-navy: #1b1d45;
    --ink-body: #3a3a3a;
    --rule: #e3e3ea;
    --rule-vertical: #c9cbd6;
    --paper-text: #ffffff;
  }
  * { margin: 0; padding: 0; box-sizing: border-box; }
  html, body {
    width: 1200px;
    height: 1184px;
    overflow: hidden;
    background: var(--backdrop);
    font-family: "Open Sans", sans-serif;
  }
  .card {
    position: absolute;
    left: 148px;
    width: 900px;
    height: 514px;
  }
  .card--front {
    top: 46px;
    background: var(--card-light);
  }
  .card--back {
    top: 627px;
    background: var(--card-dark);
    border: 3px solid var(--card-dark-edge);
  }
  .wordmark {
    position: absolute;
    left: 0;
    right: 0;
    text-align: center;
    font-weight: 800;
    letter-spacing: -2px;
    line-height: 1;
  }
  .card--front .wordmark {
    top: 92px;
    font-size: 118px;
    color: var(--ink-navy);
  }
  .card--back .wordmark {
    top: 180px;
    font-size: 170px;
    color: var(--paper-text);
  }
  .front-rule {
    position: absolute;
    left: 0;
    right: 0;
    top: 303px;
    height: 4px;
    background: var(--rule);
  }
  .front-divider {
    position: absolute;
    left: 449px;
    top: 331px;
    width: 2px;
    height: 154px;
    background: var(--rule-vertical);
  }
  .identity {
    position: absolute;
    left: 220px;
    top: 376px;
    line-height: 1.05;
  }
  .identity__name {
    font-size: 27px;
    font-weight: 700;
    color: var(--ink-navy);
    letter-spacing: 0.2px;
  }
  .identity__role {
    font-size: 26px;
    color: var(--ink-body);
  }
  .contact {
    position: absolute;
    left: 503px;
    top: 328px;
    color: var(--ink-body);
    font-size: 22px;
  }
  .contact__row {
    display: flex;
    align-items: center;
    gap: 9px;
    height: 32px;
    margin-bottom: 4px;
  }
  .contact__row--web { letter-spacing: 2.5px; }
  .contact__icon { width: 23px; height: 23px; flex: none; }
  .contact__address {
    margin-top: 10px;
    line-height: 1.12;
  }
  .back-url {
    position: absolute;
    left: 0;
    right: 0;
    top: 428px;
    text-align: center;
    font-size: 29px;
    letter-spacing: 4px;
    color: var(--paper-text);
  }
</style>
</head>
<body>
  <section class="card card--front">
    <div class="wordmark">pexla</div>
    <div class="front-rule"></div>
    <div class="front-divider"></div>
    <div class="identity">
      <div class="identity__name">MARA QUILL</div>
      <div class="identity__role">Position</div>
    </div>
    <div class="contact">
      <div class="contact__row">
        <svg class="contact__icon" viewBox="0 0 24 24" aria-hidden="true">
          <circle cx="12" cy="12" r="10.5" fill="none" stroke="#2a2a2a" stroke-width="1.8"/>
          <path d="M9.5 6.5l2 2-1.3 1.6c.6 1.6 1.8 2.9 3.3 3.6l1.5-1.3 2 2-1.4 1.8C11.5 16 8 12.6 7.8 8z" fill="#2a2a2a"/>
        </svg>
        <span>012-345-6789</span>
      </div>
      <div class="contact__row">
        <svg class="contact__icon" viewBox="0 0 24 24" aria-hidden="true">
          <rect x="1.5" y="5" width="21" height="14" fill="#2a2a2a"/>
          <path d="M2.5 6l9.5 7 9.5-7M2.5 18l7-6M21.5 18l-7-6" fill="none" stroke="#fff" stroke-width="1.4"/>
        </svg>
        <span>info@pexla.com</span>
      </div>
      <div class="contact__row contact__row--web">
        <svg class="contact__icon" viewBox="0 0 24 24" aria-hidden="true">
          <g fill="none" stroke="#2a2a2a" stroke-width="1.5">
            <circle cx="12" cy="12" r="10"/>
            <ellipse cx="12" cy="12" rx="4.5" ry="10"/>
            <path d="M2 12h20M4 6.5h16M4 17.5h16M12 2v20"/>
          </g>
        </svg>
        <span>www.pexla.com</span>
      </div>
      <div class="contact__address">Street name City Name,<br>Zipcode,012345</div>
    </div>
  </section>

  <section class="card card--back">
    <div class="wordmark">pexla</div>
    <div class="back-url">www.pexla.com</div>
  </section>
</body>
</html>
```